KDWB Business Card

Looking for a business card design to incorporate our branding. We want to only use the colors listing in the Branding Package (attached).
Updates

Target Market(s)

People who need their phone or device fixed.

Industry/Entity Type

Electronics

Contact Information for Business Card

Please use:

Brightwick Gadget Clinic LLC
4810 E Harlow Ridge Rd
Suite 417
San Antonio, TX 78163

Marcus Delgrove, Store Manager

(210) 555-0147

Requirements
Must have
• Must include the colors that are contained within the Branding Package PDF file.

```html
<!DOCTYPE html>
<html lang="en">
<head>
<meta charset="utf-8">
<title>Brightwick Gadget Clinic – Business Card</title>
<link rel="stylesheet" href="https://fonts.googleapis.com/css2?family=Arimo:wght@400;500&display=swap">
<style>
  :root {
    --bg: #b9b7bb;
    --card: #f4f4f6;
    --band: #000000;
    --orange: #f0580f;
    --ink: #1d1d1f;
    --muted: #8c8c8c;
    --photo-blue: #3f78c4;
    --photo-light: #e8e6e4;
  }
  * { box-sizing: border-box; margin: 0; padding: 0; }
  html, body { width: 1200px; height: 833px; overflow: hidden; }
  body {
    background: var(--bg);
    font-family: "Arimo", Arial, sans-serif;
    display: flex;
    align-items: center;
    justify-content: center;
    gap: 48px;
  }
  .card {
    width: 525px;
    height: 300px;
    background: var(--card);
    position: relative;
    overflow: hidden;
    box-shadow: 0 10px 28px rgba(0,0,0,.22);
  }
  .brand {
    display: flex;
    align-items: center;
    gap: 12px;
    color: var(--orange);
    font-size: 26px;
    font-weight: 400;
    white-space: nowrap;
  }
  .brand-mark {
    width: 30px;
    height: 30px;
    background: var(--orange);
    flex: none;
  }

  /* Front */
  .front-band {
    height: 96px;
    background: var(--band);
    display: flex;
    align-items: center;
    justify-content: center;
  }
  .contact {
    text-align: center;
    color: var(--ink);
    padding-top: 22px;
  }
  .contact-name { font-size: 23px; letter-spacing: .2px; }
  .contact-title { color: var(--orange); font-size: 14px; margin-top: 4px; }
  .contact-phone { font-size: 25px; letter-spacing: 1px; margin-top: 18px; }
  .contact-lines { font-size: 12.5px; line-height: 1.6; margin-top: 12px; letter-spacing: .3px; }

  /* Back */
  .back-photo {
    position: absolute;
    inset: 0;
    background: linear-gradient(160deg, var(--photo-light) 0%, #cfd2d6 35%, var(--photo-blue) 60%, #2f62a8 100%);
  }
  .back-strip {
    position: absolute;
    left: 0; right: 0;
    top: 96px;
    height: 108px;
    background: rgba(246,246,248,.96);
    border-top: 2px solid var(--photo-blue);
    border-bottom: 2px solid var(--photo-blue);
    display: flex;
    align-items: center;
    justify-content: center;
  }
</style>
</head>
<body>
  <section class="card card-back">
    <div class="back-photo" role="img" aria-label="Photo of hands repairing a smartphone on a blue work mat"></div>
    <div class="back-strip">
      <div class="brand"><span class="brand-mark"></span>Brightwick Gadget Clinic</div>
    </div>
  </section>

  <section class="card card-front">
    <header class="front-band">
      <div class="brand"><span class="brand-mark"></span>Brightwick Gadget Clinic</div>
    </header>
    <div class="contact">
      <p class="contact-name">Marcus Delgrove</p>
      <p class="contact-title">Store Manager</p>
      <p class="contact-phone">(210) 555-0147</p>
      <div class="contact-lines">
        <p>marcus@BrightwickClinic.com</p>
        <p>www.BrightwickClinic.com</p>
        <p>4810 E Harlow Ridge Rd, Suite 417, San Antonio, TX 78163</p>
      </div>
    </div>
  </section>
</body>
</html>
```